Business Cards + Flyer + Letterhead for Care Recruitment Agency

We are a recruitment agency for the health & care sector. We need designs made for business cards, A5 double-sided flyer, and a letterhead template.

Our branding message is professionalism, care, compassion, expertise. We are experts in recruitment for the care & health industry.

Our logo source files and colours are here - https://www.filevault-example.net/sh/q8rn27lpzw4xkc/BBRtLm3QPW92dKfYhNvZceLmo?dl=0

For the business card, I have attached an example we like. We want a vertical business card design, something very similar to the example given. The design should match our logo in terms of brand colors. On one side should be our logo, our website (www.holbrookelune.co.uk) and Care Recruitment Specialists written somewhere visible that fits, between our logo and the website at the bottom. On the other side should be our details.

Details on the front:

Logo with slogan
Care Recruitment Specialists
www.holbrookelune.co.uk

Details on the back:

Dominic Argyros
Managing Director

Radley Court, 40-48 Pellow St, Birmingham, B7 9QX
07612 495137
dominic@holbrookelune.co.uk
www.holbrookelune.co.uk

Nadia Holbrooke
Business Development Director

07731 284956
nadia@holbrookelune.co.uk
www.holbrookelune.co.uk

For the A5 flyer, I have attached some pictures we've used for the website, which could be used for the flyer as well. To get a better idea of our branding, please visit our website - https://holbrookelune.co.uk/

The text for the flyer is also attached.

Finally, the letterhead template should be a docx template with our logo and our identifiable branding (the same shapes and matching colours you will come up with for the business cards and flyer).

```html
<!DOCTYPE html>
<html lang="en">
<head>
<meta charset="utf-8">
<title>Holbrooke Lune Letterhead</title>
<link href="https://fonts.googleapis.com/css2?family=Montserrat:wght@500;700;800&display=swap" rel="stylesheet">
<style>
  :root {
    --navy: #1b2768;
    --navy-deep: #141d52;
    --blue: #2d5fb5;
    --sky: #6fb6ea;
    --sky-pale: #b9def6;
    --paper: #ffffff;
    --ink-light: #ffffff;
  }
  * { margin: 0; padding: 0; box-sizing: border-box; }
  html, body { width: 849px; height: 1200px; overflow: hidden; background: var(--paper); }
  .letterhead {
    position: relative;
    width: 849px;
    height: 1200px;
    background: var(--paper);
    font-family: "Montserrat", Arial, sans-serif;
    overflow: hidden;
  }
  .brand {
    position: absolute;
    left: 34px;
    top: 30px;
    width: 220px;
    display: flex;
    flex-direction: column;
    align-items: center;
    gap: 12px;
  }
  .brand-dot {
    width: 56px;
    height: 56px;
    border-radius: 50%;
    background: var(--sky);
  }
  .brand-name {
    font-weight: 800;
    font-size: 18px;
    letter-spacing: 1px;
    color: var(--navy);
    line-height: 1;
    white-space: nowrap;
  }
  .company-header {
    position: absolute;
    left: 305px;
    top: 44px;
  }
  .company-tagline {
    font-weight: 800;
    font-size: 24px;
    color: var(--navy);
    letter-spacing: 0.6px;
    line-height: 1.1;
  }
  .company-address {
    margin-top: 6px;
    font-weight: 500;
    font-size: 20px;
    color: var(--blue);
    line-height: 1.3;
  }
  .footer-waves {
    position: absolute;
    left: 0;
    top: 960px;
    width: 849px;
    height: 240px;
    display: block;
  }
  .contact-list {
    position: absolute;
    left: 40px;
    top: 1076px;
    list-style: none;
  }
  .contact-item {
    display: flex;
    align-items: center;
    gap: 12px;
    height: 34px;
    font-weight: 500;
    font-size: 17px;
    color: var(--ink-light);
  }
  .contact-icon {
    width: 22px;
    height: 22px;
    flex: none;
  }
</style>
</head>
<body>
<main class="letterhead">
  <div class="brand">
    <span class="brand-dot"></span>
    <span class="brand-name">HOLBROOKE LUNE</span>
  </div>

  <header class="company-header">
    <p class="company-tagline">CARE RECRUITMENT SPECIALISTS</p>
    <p class="company-address">Radley Court, 40-48 Pellow St,<br>Birmingham, B7 9QX</p>
  </header>

  <svg class="footer-waves" viewBox="0 0 849 240" preserveAspectRatio="none" aria-hidden="true">
    <defs>
      <linearGradient id="wave-sky" x1="0" y1="0" x2="1" y2="0">
        <stop offset="0" stop-color="#b9def6"/>
        <stop offset="1" stop-color="#6fb6ea"/>
      </linearGradient>
      <linearGradient id="wave-navy" x1="0" y1="0" x2="0" y2="1">
        <stop offset="0" stop-color="#1f2d78"/>
        <stop offset="1" stop-color="#141d52"/>
      </linearGradient>
    </defs>
    <path d="M0 70 C 200 120, 420 40, 600 40 C 720 40, 800 20, 849 0 L849 240 L0 240 Z" fill="url(#wave-sky)" opacity="0.6"/>
    <path d="M0 95 C 220 140, 430 70, 620 65 C 730 62, 810 45, 849 30 L849 240 L0 240 Z" fill="url(#wave-sky)"/>
    <path d="M0 110 C 240 150, 440 95, 640 92 C 740 90, 810 78, 849 68 L849 240 L0 240 Z" fill="#2d5fb5"/>
    <path d="M0 122 C 250 160, 450 115, 650 112 C 750 110, 815 100, 849 94 L849 240 L0 240 Z" fill="url(#wave-navy)"/>
  </svg>

  <ul class="contact-list">
    <li class="contact-item">
      <svg class="contact-icon" viewBox="0 0 24 24" aria-hidden="true"><circle cx="12" cy="12" r="11" fill="none" stroke="#fff" stroke-width="1.5"/><path d="M8.5 6.5l2 2-1.2 1.6c.8 1.7 2 2.9 3.6 3.6l1.6-1.2 2 2-1.3 2c-4.3-.4-7.900-4-8.3-8.3z" fill="#fff"/></svg>
      <span>07612 495137</span>
    </li>
    <li class="contact-item">
      <svg class="contact-icon" viewBox="0 0 24 24" aria-hidden="true"><circle cx="12" cy="12" r="11" fill="none" stroke="#fff" stroke-width="1.5"/><rect x="6.5" y="8" width="11" height="8" rx="1" fill="none" stroke="#fff" stroke-width="1.4"/><path d="M6.8 8.5l5.2 4 5.2-4" fill="none" stroke="#fff" stroke-width="1.4"/></svg>
      <span>dominic@holbrookelune.co.uk</span>
    </li>
    <li class="contact-item">
      <svg class="contact-icon" viewBox="0 0 24 24" aria-hidden="true"><circle cx="12" cy="12" r="11" fill="none" stroke="#fff" stroke-width="1.5"/><path d="M9 12h6M13 9.5l2.5 2.5-2.5 2.5" fill="none" stroke="#fff" stroke-width="1.6" stroke-linecap="round" stroke-linejoin="round"/></svg>
      <span>www.holbrookelune.co.uk</span>
    </li>
  </ul>
</main>
</body>
</html>
```